American cannabis tech company business card design

Pavrel.com is seeking a modern, professional, and brand-aligned business card that represents our company and its core values: Mission, Story, Values, and Impact. As an innovative cannabis company, we want a business card that is not only visually appealing but also serves as a representation of who we are and what we stand for.

Project Scope: Design a double-sided business card that integrates our brand identity and core values. Incorporate our key brand elements, ensuring a sleek and contemporary aesthetic. Visually reflect our core values (Mission, Story, Values, Impact) in a way that is engaging yet professional.

Target Market(s)

Vendors, third parties,

Contact Information for Business Card

Contact details (name, title, email, phone, website, etc.)

Font styles to use
Other font styles liked:
• Caslon, Centra

Colors

Designer to choose colors to be used in the design.

Requirements
Must have
• Pavrel.com logo and branding A creative yet clean way to integrate our core values (Mission, Story, Values, Impact) Modern typography and a well-structured layout
Nice to have
• forest green, grey, white, black
Should not have
• references to marijuana, leafs, plants, or related product

```html
<!DOCTYPE html>
<html lang="en">
<head>
<meta charset="UTF-8">
<title>Pavrel.com Business Card</title>
<link href="https://fonts.googleapis.com/css2?family=Lato:wght@400;700;900&display=swap" rel="stylesheet">
<style>
  :root {
    --backdrop: #1b1c1b;
    --forest-light: #1e7536;
    --forest: #14572a;
    --forest-deep: #0f3a1d;
    --band-top: #225228;
    --band-bottom: #15301a;
    --paper: #ffffff;
    --wordmark-dark: #1a4d25;
    --silver: #e4e4e4;
    --ink-light: #ffffff;
    --divider: rgba(255,255,255,0.35);
  }
  * { margin: 0; padding: 0; box-sizing: border-box; }
  html, body {
    width: 1200px; height: 1015px; overflow: hidden;
    background: var(--backdrop);
    font-family: "Lato", sans-serif;
  }
  .canvas {
    width: 1200px; height: 1015px;
    display: flex; flex-direction: column; align-items: center; justify-content: center;
    gap: 44px;
  }
  .card {
    width: 760px; height: 434px;
    position: relative; overflow: hidden;
    box-shadow: 0 10px 30px rgba(0,0,0,0.5);
  }
  .wordmark {
    font-family: "Lato", sans-serif;
    font-weight: 900;
    font-size: 92px;
    letter-spacing: 2px;
    line-height: 1;
  }

  /* Front */
  .card-front {
    background: linear-gradient(160deg, var(--forest-light) 0%, var(--forest) 55%, var(--forest-deep) 100%);
    display: flex; align-items: center; justify-content: center;
  }
  .card-front .wordmark { color: var(--silver); }

  /* Back */
  .card-back { background: var(--paper); }
  .back-logo-area {
    position: absolute; left: 0; top: 0; width: 100%; height: 232px;
    display: flex; align-items: center; justify-content: center;
  }
  .back-logo-area .wordmark { color: var(--wordmark-dark); padding-top: 24px; }
  .accent-rule {
    position: absolute; left: 0; top: 246px; width: 100%; height: 3px;
    background: var(--band-top);
  }
  .contact-band {
    position: absolute; left: 0; top: 256px; width: 100%; bottom: 0;
    background: linear-gradient(180deg, var(--band-top) 0%, var(--band-bottom) 100%);
    display: flex; align-items: center;
    color: var(--ink-light);
  }
  .identity {
    width: 312px; text-align: right; padding-right: 28px;
  }
  .identity .person-name {
    font-weight: 700; font-size: 26px; letter-spacing: 1px; text-transform: uppercase;
  }
  .identity .person-role {
    font-weight: 400; font-size: 19px; margin-top: 2px;
  }
  .band-divider {
    width: 1px; height: 110px; background: var(--divider);
  }
  .contact-list {
    list-style: none; padding-left: 26px;
    display: flex; flex-direction: column; gap: 8px;
    font-size: 19px; font-weight: 400;
  }
  .contact-list li { display: flex; align-items: center; gap: 10px; }
  .contact-list svg { width: 20px; height: 20px; flex: none; }
</style>
</head>
<body>
<main class="canvas">
  <section class="card card-front" aria-label="Card front">
    <div class="wordmark">PAVREL</div>
  </section>

  <section class="card card-back" aria-label="Card back">
    <div class="back-logo-area">
      <div class="wordmark">PAVREL</div>
    </div>
    <div class="accent-rule"></div>
    <div class="contact-band">
      <div class="identity">
        <div class="person-name">Daniel Carter</div>
        <div class="person-role">Managing Director</div>
      </div>
      <div class="band-divider"></div>
      <ul class="contact-list">
        <li>
          <svg viewBox="0 0 24 24" aria-hidden="true"><path fill="#fff" d="M6.6 10.8a15.1 15.1 0 0 0 6.6 6.6l2.2-2.2c.3-.3.7-.4 1-.2 1.1.4 2.3.6 3.6.6.6 0 1 .4 1 1V20c0 .6-.4 1-1 1C10.6 21 3 13.4 3 4c0-.6.4-1 1-1h3.5c.6 0 1 .4 1 1 0 1.3.2 2.5.6 3.6.1.3 0 .7-.2 1l-2.3 2.2z"/></svg>
          <span>044-555 210 384</span>
        </li>
        <li>
          <svg viewBox="0 0 24 24" aria-hidden="true"><rect x="2" y="5" width="20" height="14" fill="#fff"/><path d="M2 5l10 8 10-8" fill="none" stroke="#1e4a24" stroke-width="1.8"/></svg>
          <span>info@pavrel.com</span>
        </li>
        <li>
          <svg viewBox="0 0 24 24" aria-hidden="true"><g fill="none" stroke="#fff" stroke-width="1.8"><circle cx="12" cy="12" r="9.5"/><ellipse cx="12" cy="12" rx="4.2" ry="9.5"/><path d="M2.5 12h19M4 7h16M4 17h16"/></g></svg>
          <span>www.pavrel.com</span>
        </li>
      </ul>
    </div>
  </section>
</main>
</body>
</html>
```